Modern Business Card

Modern professional business card with more than just logo and demographic info. Something memorable.

We are a trendy/modern chiropractic group with an emphasis on neurology, hence the minimalist-type brain logo. We want to convey that modern and technical aspect with professionalism and the elite nature of our practice environment.

```html
<!DOCTYPE html>
<html lang="en">
<head>
<meta charset="utf-8">
<title>Keystone Chiropractic – Business Card</title>
<link rel="stylesheet" href="https://fonts.googleapis.com/css2?family=Cinzel:wght@500&family=Montserrat:wght@400;500&display=swap">
<style>
  :root {
    --page: #1b1b1c;
    --card: #262627;
    --card-edge: #2e2e30;
    --map: rgba(255,255,255,0.045);
    --white: #f4f4f4;
    --muted: #d9d9d9;
    --blue: #4a86d4;
  }
  * { margin: 0; padding: 0; box-sizing: border-box; }
  html, body { width: 1200px; height: 900px; overflow: hidden; background: var(--page); }
  .canvas { position: relative; width: 1200px; height: 900px; }
  .card {
    position: absolute; left: 250px; width: 700px; height: 400px;
    background: linear-gradient(160deg, var(--card-edge), var(--card) 60%);
    box-shadow: 0 18px 40px rgba(0,0,0,0.55);
    overflow: hidden;
  }
  .card--front { top: 40px; }
  .card--back { top: 470px; }
  .map-area {
    position: absolute; inset: 30px 40px;
    background: radial-gradient(ellipse at 50% 45%, var(--map), transparent 70%);
    border-radius: 40%;
  }
  .brand { position: absolute; display: flex; align-items: center; gap: 14px; }
  .brand__mark { width: 22px; height: 22px; background: var(--blue); flex: none; }
  .brand__name {
    font-family: "Cinzel", serif; font-weight: 500; color: var(--white);
    line-height: 1.05; letter-spacing: 1px;
  }
  .card--front .brand { left: 50%; top: 50%; transform: translate(-50%, -50%); }
  .card--front .brand__mark { width: 30px; height: 30px; }
  .card--front .brand__name { font-size: 44px; }
  .card--back .brand { right: 40px; top: 48px; }
  .card--back .brand__name { font-size: 28px; }
  .person { position: absolute; left: 44px; top: 150px; }
  .person__name {
    font-family: "Cinzel", serif; font-weight: 500; color: var(--blue);
    font-size: 24px; letter-spacing: 0.5px;
  }
  .person__role { font-family: "Montserrat", sans-serif; color: var(--muted); font-size: 16px; margin-top: 4px; }
  .divider { position: absolute; left: 44px; right: 70px; top: 226px; height: 2px; background: var(--blue); }
  .contact { position: absolute; left: 44px; top: 250px; list-style: none;
    font-family: "Montserrat", sans-serif; font-size: 18px; color: var(--muted); }
  .contact li { display: flex; align-items: center; gap: 12px; height: 30px; }
  .contact svg { width: 15px; height: 15px; flex: none; }
  .contact .accent { color: var(--blue); }
  .address { position: absolute; right: 70px; bottom: 40px; text-align: right;
    font-family: "Montserrat", sans-serif; font-size: 18px; color: var(--muted); line-height: 1.45; }
</style>
</head>
<body>
<div class="canvas">
  <section class="card card--front">
    <div class="map-area" role="img" aria-label="Faint world map in the card background"></div>
    <div class="brand">
      <span class="brand__mark"></span>
      <div class="brand__name">KEYSTONE<br>CHIROPRACTIC</div>
    </div>
  </section>

  <section class="card card--back">
    <div class="map-area" role="img" aria-label="Faint world map in the card background"></div>
    <div class="brand">
      <span class="brand__mark"></span>
      <div class="brand__name">KEYSTONE<br>CHIROPRACTIC</div>
    </div>
    <div class="person">
      <div class="person__name">DANIEL MERCER</div>
      <div class="person__role">Director</div>
    </div>
    <div class="divider"></div>
    <ul class="contact">
      <li>
        <svg viewBox="0 0 16 16"><path d="M4 1.5 6 5 4.6 6.4a8 8 0 0 0 5 5L11 10l3.5 2-1 2.5C7 14.5 1.5 9 1.5 2.5Z" fill="var(--blue)"/></svg>
        (555) 014-2286
      </li>
      <li>
        <svg viewBox="0 0 16 16"><rect x="1.5" y="3.5" width="13" height="9" fill="none" stroke="var(--blue)" stroke-width="1.4"/><path d="m1.5 3.5 6.5 5 6.5-5" fill="none" stroke="var(--blue)" stroke-width="1.4"/></svg>
        info@keystonechiro.com
      </li>
      <li>
        <svg viewBox="0 0 16 16"><circle cx="8" cy="8" r="6.5" fill="none" stroke="var(--blue)" stroke-width="1.3"/><ellipse cx="8" cy="8" rx="2.8" ry="6.5" fill="none" stroke="var(--blue)" stroke-width="1.1"/><path d="M1.5 8h13M2.5 5h11M2.5 11h11" stroke="var(--blue)" stroke-width="1"/></svg>
        <span>www.<span class="accent">keystonechiro</span>.com</span>
      </li>
    </ul>
    <address class="address" style="font-style:normal">1187 Linden Ridge<br>Salem, OR 97301</address>
  </section>
</div>
</body>
</html>
```